WE ARE BRIGHT SPARROW, building a full website with ecommerce

requirements:
CODED FOR SITEQUILL
ONLINE STORE FUNCTION WITH E-COMMERCE USING TRADEBLOOM
PAGEWAVE AND PICTOLANE LINKS

I need a website design for my organization, WE ARE BRIGHT SPARROW, a global empowerment movement elevating woman, and the world. The site's home page should reflect our mission, to empower women. It should have a strong, empowering feel, with minimalistic design.
Please see www.lunavelto.com and http://www.corvenhal.co/ for an inspiration on layout and feel.

**PLEASE SEE ATTACHMENT "LOGO MOCK UP" FOR LOGO. THIS IS NOT THE FINAL VECTOR FILE, BUT THIS LOOKS THE SAME AS THE FINAL LOGO.

HOME PAGE:
The first section of the home page should include a background image with our logo center.

You should include the following links to pages at the top right of the page:
MISSION
MANTRA
ARMOR
MEET BS (I would like "bs" to be our logo)
pagewave and pictolane links

As you scroll down the page, you should see the following sections, which correlate to the links to pages as written above. **SEE ATTACHED SKETCH "HOMEPAGE LAYOUT IDEA" FOR REFERENCE**

WHO WE ARE (correlates to the link Mission)

OUR MANTRA (correlates to the link Mantra)

OUR ARMOR (correlates to the link The Shirt)
(This is where we will sell a shirt (and other apparel) and need the e-commerce function)

MEET BRIGHT SPARROWS (correlates to the link Meet BS)

SHOW OFF YOUR SUPER POWERS (correlates to the pagewave and pictolane)

FEATURED BRIGHT SPARROW (no link on top right of page)

On the homepage, for each of the above sections, as you scroll down there should be an image, either in the background or framed, next to the title (WHO WE ARE, for example), as well as one sentence of small text explaining the title. The title (WHO WE ARE) and the one sentence should link to a page (ie WHO WE ARE + the one sentence links to the MISSION page). ** SEE ATTACHED SKETCH "HOMEPAGE SECTION IDEAS" FOR REFERENCE**

**PLEASE SEE ATTACHMENT "WEBSITE TITLE IDEAS" FOR A STARTING PLACE OF THE LOOK. These don't have to be exact, but they give you an idea of what I'm looking for.

**FONTS TYPOLD EXTRA BOLD AND TYPOLD BOOK 500 (WHICH SHOULD BE BOLDED MANUALLY) ARE ATTACHED**

Target Market(s)

Women, mainly in US

Industry/Entity Type

Social

Coding

Coded - Design and coding required

Number of Pages Required

5+ page

Font styles to use
Other font styles liked:
• Typol Extra Bold

Requirements
Must have
• CODED FOR SITEQUILL
• ONLINE STORE FUNCTION WITH E-COMMERCE USING TRADEBLOOM
• PAGEWAVE AND PICTOLANE LINKS
• Typold Extra Bold and Typold Book 500, attached
• please see description for all requirements
Nice to have
• please see description for all ideas
Should not have

```html
<!DOCTYPE html>
<html lang="en">
<head>
<meta charset="utf-8">
<title>We Are Bright Sparrow</title>
<link href="https://fonts.googleapis.com/css2?family=Montserrat:wght@600;700;800&family=Open+Sans:wght@400;600&display=swap" rel="stylesheet">
<style>
  :root{
    --teal:#2bb5a0;
    --teal-dark:#1fa390;
    --ink:#141414;
    --white:#ffffff;
    --muted:#555a5e;
    --hero-shade:rgba(20,22,26,.55);
  }
  *{box-sizing:border-box;margin:0;padding:0}
  html,body{width:1200px;height:4147px;overflow:hidden;background:var(--white)}
  body{font-family:"Open Sans",Arial,sans-serif;color:var(--ink)}
  .page{position:relative;width:1200px;height:4147px}

  /* neutral brand placeholder: one plain circle */
  .dot{display:block;flex:none;border:6px solid currentColor;border-radius:50%}

  /* hero */
  .hero{position:relative;height:697px;overflow:hidden;color:var(--white)}
  .hero-photo{position:absolute;inset:0;background:linear-gradient(115deg,#6b6a66 0%,#8b8478 35%,#5b5e60 60%,#3c3f42 100%)}
  .hero-photo::after{content:"";position:absolute;inset:0;background:var(--hero-shade)}
  .topbar{position:absolute;top:30px;left:97px;right:97px;display:flex;justify-content:space-between;align-items:center;z-index:2}
  .brand{display:flex;align-items:center;gap:12px}
  .brand .dot{width:40px;height:40px;border-width:4px}
  .brand-name{font-family:"Montserrat",sans-serif;font-weight:800;font-size:18px;line-height:1.05}
  .nav{display:flex;align-items:center;gap:22px;font-family:"Montserrat",sans-serif;font-weight:700;font-size:14px;letter-spacing:.5px}
  .nav .social{font-size:10px;border:2px solid var(--white);padding:4px 8px;border-radius:14px}
  .arrow{position:absolute;top:340px;width:26px;height:50px;z-index:2}
  .arrow.left{left:68px}.arrow.right{right:68px}
  .hero-center{position:absolute;top:200px;left:0;right:0;text-align:center;z-index:2;display:flex;flex-direction:column;align-items:center}
  .hero-center .dot{width:120px;height:120px;border-width:10px}
  .hero-title{margin-top:34px;font-family:"Montserrat",sans-serif;font-weight:800;font-size:32px;line-height:1.3}
  .signup{margin-top:28px;width:594px;height:40px;display:flex;background:var(--white);border-radius:3px;overflow:hidden}
  .signup .field{flex:1;padding-left:14px;display:flex;align-items:center;font-size:12px;color:#8a8f93}
  .signup .btn{width:150px;background:var(--teal);display:flex;align-items:center;justify-content:center;font-family:"Montserrat",sans-serif;font-weight:700;font-size:13px;color:var(--white)}

  /* mission band */
  .mission{height:282px;background:linear-gradient(180deg,var(--teal),var(--teal-dark));color:var(--white);text-align:center;padding-top:42px}
  .mission p{font-family:"Montserrat",sans-serif;font-weight:800;font-size:26px;line-height:1.42;letter-spacing:.5px}
  .mission .fly{margin-top:18px;display:inline-flex;align-items:center;gap:10px;font-family:"Montserrat",sans-serif;font-weight:800;font-size:26px;line-height:1}
  .mission .fly .dot{width:30px;height:30px;border-width:3px}

  /* feature sections */
  .feature{position:relative;height:498px;overflow:hidden}
  .feature .photo{position:absolute;inset:0}
  .feature.text-left .photo{clip-path:polygon(50% 0,100% 0,100% 100%,46% 100%)}
  .feature.text-right .photo{clip-path:polygon(0 0,46% 0,54% 100%,0 100%)}
  .feature.full .photo{clip-path:none}
  .copy{position:absolute;top:0;bottom:0;width:440px;display:flex;flex-direction:column;justify-content:center}
  .text-left .copy{left:97px}
  .text-right .copy,.full .copy{left:680px}
  .heading{display:flex;align-items:center;gap:22px}
  .heading .dot{width:100px;height:100px;border-width:9px}
  .heading h2{font-family:"Montserrat",sans-serif;font-weight:800;font-size:44px;line-height:1.02;letter-spacing:-.5px}
  .heading h2 small{display:block;font-size:26px;font-weight:800;margin-bottom:4px}
  .copy p{margin-top:36px;font-size:11px;line-height:1.9;color:var(--muted)}
  .shop{margin-top:22px;align-self:flex-start;background:var(--teal);color:var(--white);font-family:"Montserrat",sans-serif;font-weight:700;font-size:11px;padding:9px 20px;border-radius:16px}
  .pills{margin-top:30px;margin-left:122px;display:flex;gap:14px}
  .pills span{background:var(--teal);color:var(--white);font-family:"Montserrat",sans-serif;font-weight:700;font-size:10px;padding:7px 12px;border-radius:3px}

  /* footer */
  .footer{position:absolute;left:0;right:0;bottom:0;height:182px;background:var(--teal);color:var(--white);text-align:center;padding-top:34px}
  .footer .socials{display:flex;justify-content:center;gap:12px}
  .footer .socials span{font-family:"Montserrat",sans-serif;font-weight:700;font-size:10px;border:2px solid var(--white);padding:4px 9px;border-radius:14px}
  .footer nav{margin-top:20px;font-size:13px;font-weight:600;word-spacing:4px}
  .footer small{display:block;margin-top:12px;font-size:11px}
</style>
</head>
<body>
<div class="page">

  <header class="hero">
    <div class="hero-photo" role="img" aria-label="Background photo of a smiling woman seated in a bright office"></div>
    <div class="topbar">
      <div class="brand">
        <span class="dot"></span>
        <div class="brand-name">WE ARE<br>BRIGHT SPARROW</div>
      </div>
      <nav class="nav">
        <span>MISSION</span><span>MANTRA</span><span>MEET BS</span><span>THE SHIRT</span>
        <span class="social">PAGEWAVE</span><span class="social">PICTOLANE</span>
      </nav>
    </div>
    <svg class="arrow left" viewBox="0 0 26 50"><polyline points="22,3 4,25 22,47" fill="none" stroke="#fff" stroke-width="2"/></svg>
    <svg class="arrow right" viewBox="0 0 26 50"><polyline points="4,3 22,25 4,47" fill="none" stroke="#fff" stroke-width="2"/></svg>
    <div class="hero-center">
      <span class="dot"></span>
      <h1 class="hero-title">WE ARE BRIGHT SPARROW<br>AND I WILL CONQUER THE WORLD</h1>
      <div class="signup"><div class="field">hello@brightsparrow.org</div><div class="btn">LET'S FLY</div></div>
    </div>
  </header>

  <section class="mission">
    <p>WE ARE BRIGHT SPARROW IS A GLOBAL<br>EMPOWERMENT MOVEMENT ELEVATING WOMEN...<br>AND THE WORLD.</p>
    <div class="fly"><span class="dot"></span>LET'S FLY</div>
  </section>

  <section class="feature text-left">
    <div class="photo" role="img" aria-label="Photo of a woman on the phone working at a laptop by a window" style="background:linear-gradient(120deg,#c9b9a2,#8e7a66 55%,#5c4a3c)"></div>
    <div class="copy">
      <div class="heading"><span class="dot"></span><h2>WHO<br>WE<br>ARE</h2></div>
      <p>We are women lifting women, building courage in every city we reach. Each story shared here sparks another, and together we grow stronger, braver and kinder every single day.</p>
    </div>
  </section>

  <section class="feature text-right">
    <div class="photo" role="img" aria-label="Photo of a confident woman with crossed arms outdoors among autumn trees" style="background:linear-gradient(150deg,#b49a6a,#7e7a58 45%,#3d4d6e)"></div>
    <div class="copy">
      <div class="heading"><span class="dot"></span><h2>OUR<br>MANTRA</h2></div>
      <p>We are women lifting women, building courage in every city we reach. Each story shared here sparks another, and together we grow stronger, braver and kinder every single day.</p>
    </div>
  </section>

  <section class="feature text-left">
    <div class="photo" role="img" aria-label="Photo of two women talking over coffee in a warm cafe" style="background:linear-gradient(120deg,#a0553a,#c58a62 45%,#6d4a3c)"></div>
    <div class="copy">
      <div class="heading"><span class="dot"></span><h2>MEET<br>BRIGHT<br>SPARROWS</h2></div>
      <p>We are women lifting women, building courage in every city we reach. Each story shared here sparks another, and together we grow stronger, braver and kinder every single day.</p>
    </div>
  </section>

  <section class="feature full">
    <div class="photo" role="img" aria-label="Photo of a woman in the movement's black shirt leaning on a bicycle against a concrete wall" style="background:linear-gradient(90deg,#b3b1ac,#cdcbc6 55%,#d9d7d2)"></div>
    <div class="copy">
      <div class="heading"><span class="dot"></span><h2>OUR<br>ARMOR</h2></div>
      <p>We are women lifting women, building courage in every city we reach. Each story shared here sparks another, and together we grow stronger, braver and kinder every single day.</p>
      <span class="shop">SHOP NOW ›</span>
    </div>
  </section>

  <section class="feature text-left">
    <div class="photo" role="img" aria-label="Photo of hands holding a tablet and phone over a table with colourful paper speech bubbles" style="background:linear-gradient(130deg,#3fa7c9,#d88b4a 50%,#8a5d3f)"></div>
    <div class="copy">
      <div class="heading"><span class="dot"></span><h2><small>SHOW OFF YOUR</small>SUPER<br>POWERS</h2></div>
      <div class="pills"><span>PAGEWAVE</span><span>PICTOLANE</span></div>
    </div>
  </section>

  <section class="feature text-right">
    <div class="photo" role="img" aria-label="Photo of a smiling woman in a hat and striped top with a bicycle on a city street" style="background:linear-gradient(140deg,#c7b7a4,#8f7d6c 50%,#4d4646)"></div>
    <div class="copy">
      <div class="heading"><span class="dot"></span><h2>FEATURED<br>BRIGHT<br>SPARROWS</h2></div>
      <p>We are women lifting women, building courage in every city we reach. Each story shared here sparks another, and together we grow stronger, braver and kinder every single day.</p>
    </div>
  </section>

  <footer class="footer">
    <div class="socials"><span>PAGEWAVE</span><span>PICTOLANE</span></div>
    <nav>Home / Mission / Mantra / Meet / The Shirt</nav>
    <small>Copyright © 2017. We Are Bright Sparrow. All Rights Reserved.</small>
  </footer>

</div>
</body>
</html>
```